Timber Crest Construction Needs business card

Hey we are in need of business card designs. I have upload our logo as a guideline, but free feel to run with it or come up with something unique.
Pls have fun with it and be creative. the name says it all!
i will give some directions after i see a few entries..
Updates
Logo source file has been uploaded..
Hey because of the logo is so colourful already.
Can we have a few submissions with less colour.
Also we are looking for clever/hidden/descriptive business card.

```html
<!DOCTYPE html>
<html lang="en">
<head>
<meta charset="utf-8">
<title>Timber Crest Construction – Business Card</title>
<link rel="stylesheet" href="https://fonts.googleapis.com/css2?family=Questrial&family=Arimo:wght@400;700&display=swap">
<style>
  :root {
    --page-bg: #e7e4e0;
    --card-white: #ffffff;
    --ink-grey: #5b5d60;
    --ink-dark: #222222;
    --brand-blue: #2f5fae;
    --brand-blue-deep: #1f3f8a;
    --brand-blue-light: #4c8be0;
    --swoosh-black: #111111;
    --text-on-blue: #ffffff;
    --stripe-light: #e3ecf6;
    --shadow: rgba(0, 0, 0, 0.18);
  }
  * { box-sizing: border-box; margin: 0; padding: 0; }
  html, body { width: 1200px; height: 470px; overflow: hidden; }
  body {
    background: var(--page-bg);
    font-family: "Arimo", Arial, sans-serif;
    position: relative;
  }
  .card {
    position: absolute;
    top: 75px;
    width: 540px;
    height: 320px;
    background: var(--card-white);
    box-shadow: 0 6px 18px var(--shadow);
    overflow: hidden;
  }
  .card--front { left: 40px; }
  .card--back { left: 620px; }

  /* Wordmark */
  .wordmark {
    display: flex;
    align-items: center;
    gap: 12px;
    font-family: "Questrial", "Century Gothic", sans-serif;
    color: var(--ink-grey);
    font-weight: 400;
    white-space: nowrap;
  }
  .wordmark__square {
    width: 26px; height: 26px;
    background: var(--ink-grey);
    flex: none;
  }
  .wordmark__name { font-size: 30px; letter-spacing: 0.5px; line-height: 1; }

  .card--front .wordmark {
    position: absolute;
    left: 0; right: 0; top: 68px;
    justify-content: center;
  }

  /* Front blue band */
  .front-band { position: absolute; left: 0; top: 0; width: 540px; height: 320px; }

  .contact-person {
    position: absolute;
    right: 288px;
    top: 198px;
    text-align: right;
    color: var(--text-on-blue);
  }
  .contact-person__name { font-size: 19px; line-height: 1.1; }
  .contact-person__title { font-size: 14px; margin-bottom: 22px; }
  .contact-person__address { font-size: 13.5px; line-height: 1.25; }

  .contact-divider {
    position: absolute;
    left: 265px; top: 196px;
    width: 1px; height: 100px;
    background: var(--text-on-blue);
    opacity: 0.85;
  }
  .contact-list {
    position: absolute;
    left: 278px; top: 188px;
    list-style: none;
    color: var(--text-on-blue);
    font-size: 14px;
  }
  .contact-list li {
    display: flex; align-items: center; gap: 6px;
    height: 22px;
  }
  .contact-list svg { width: 12px; height: 12px; flex: none; }

  /* Back */
  .back-decoration {
    position: absolute;
    left: 80px; top: 20px;
    width: 400px; height: 270px;
    background: radial-gradient(ellipse at center, #f1f4f7 0%, #f6f6f3 55%, #ffffff 100%);
  }
  .card--back .wordmark {
    position: absolute;
    left: 0; right: 0; top: 120px;
    justify-content: center;
  }
  .back-url {
    position: absolute;
    left: 0; right: 0; top: 166px;
    text-align: center;
    font-size: 19px;
    color: var(--ink-dark);
  }
  .back-stripe {
    position: absolute;
    left: 0; right: 0; bottom: 22px;
    height: 14px;
    background: linear-gradient(to bottom, var(--stripe-light) 0 4px, transparent 4px 8px, var(--stripe-light) 8px 14px);
  }
</style>
</head>
<body>

  <section class="card card--front" aria-label="Business card front">
    <div class="wordmark">
      <span class="wordmark__square"></span>
      <span class="wordmark__name">TIMBER CREST CONSTRUCTION</span>
    </div>

    <svg class="front-band" viewBox="0 0 540 320" aria-hidden="true">
      <defs>
        <radialGradient id="bandGradient" cx="0.55" cy="0.2" r="0.8">
          <stop offset="0" stop-color="var(--brand-blue-light)"/>
          <stop offset="0.5" stop-color="var(--brand-blue)"/>
          <stop offset="1" stop-color="var(--brand-blue-deep)"/>
        </radialGradient>
      </defs>
      <path d="M0 228 C 120 150, 300 118, 540 150 L540 140 C 300 104, 110 138, 0 214 Z" fill="var(--swoosh-black)"/>
      <path d="M0 236 C 120 160, 300 130, 540 158 L540 320 L0 320 Z" fill="url(#bandGradient)"/>
    </svg>

    <div class="contact-person">
      <p class="contact-person__name">Your Name</p>
      <p class="contact-person__title">Title</p>
      <p class="contact-person__address">Street Name City Name<br>State Zipcode</p>
    </div>

    <span class="contact-divider"></span>

    <ul class="contact-list">
      <li>
        <svg viewBox="0 0 12 12"><circle cx="6" cy="6" r="5.5" fill="none" stroke="#fff"/><path d="M4 3.2 L5 4.6 L4.5 5.2 Q5.4 6.8 6.8 7.5 L7.4 7 L8.8 8 L8.2 9 Q5.5 8.8 3.2 4.2 Z" fill="#fff"/></svg>
        0400 555 018
      </li>
      <li>
        <svg viewBox="0 0 12 12"><circle cx="6" cy="6" r="5.5" fill="none" stroke="#fff"/><path d="M4 3.2 L5 4.6 L4.5 5.2 Q5.4 6.8 6.8 7.5 L7.4 7 L8.8 8 L8.2 9 Q5.5 8.8 3.2 4.2 Z" fill="#fff"/></svg>
        0400 555 018
      </li>
      <li>
        <svg viewBox="0 0 12 12"><rect x="0.5" y="2.5" width="11" height="8" rx="1" fill="#fff"/><path d="M0.8 3 L6 7 L11.2 3" fill="none" stroke="var(--brand-blue)" stroke-width="1"/></svg>
        hello@timbercrestbuild.com
      </li>
      <li>
        <svg viewBox="0 0 12 12" fill="none" stroke="#fff"><circle cx="6" cy="6" r="5.2"/><ellipse cx="6" cy="6" rx="2.2" ry="5.2"/><path d="M0.8 6 H11.2"/></svg>
        www.timbercrestbuild.com
      </li>
    </ul>
  </section>

  <section class="card card--back" aria-label="Business card back">
    <div class="back-decoration" role="img" aria-label="Faint enlarged company mark in pale pastel tones behind the name"></div>
    <div class="wordmark">
      <span class="wordmark__square"></span>
      <span class="wordmark__name">TIMBER CREST CONSTRUCTION</span>
    </div>
    <p class="back-url">www.timbercrestbuild.com</p>
    <span class="back-stripe"></span>
  </section>

</body>
</html>
```